Business Card Design

We need a business card designed for our new company. Prefer a black card with white logo & writing.

Contact Information for Business Card

Ted Galloway, address: 7-4812 Fernhollow Road, Abbotsford, BC, V3K 8R2, Office Phone: 604-712-3390, Cell: 604-947-2164, Email: ted@resinworkshub.ca

Colors

Designer to choose only greyscale colors for use in the design.

```html
<!DOCTYPE html>
<html lang="en">
<head>
<meta charset="utf-8">
<title>Resinworks Hub – Business Card</title>
<link rel="stylesheet" href="https://fonts.googleapis.com/css2?family=Montserrat:wght@300;400;700&display=swap">
<style>
  :root {
    --bg: #2a2c30;
    --card: #1d1d1f;
    --card-gloss: #0d0d0e;
    --white: #ffffff;
    --muted: #9a9a9a;
    --ink: #141414;
  }
  * { box-sizing: border-box; margin: 0; padding: 0; }
  html, body { width: 1200px; height: 900px; overflow: hidden; }
  body {
    background: var(--bg);
    font-family: "Montserrat", Arial, sans-serif;
    position: relative;
  }
  .card {
    position: absolute;
    top: 135px;
    width: 360px;
    height: 630px;
    border-radius: 28px;
    background: var(--card);
    overflow: hidden;
    box-shadow: 0 20px 40px rgba(0,0,0,.45);
  }
  .card--front { left: 190px; }
  .card--back { left: 650px; display: flex; align-items: center; justify-content: center; }

  .card__curve { position: absolute; inset: 0; width: 100%; height: 100%; }

  .holder { position: absolute; left: 40px; top: 44px; }
  .holder__name { color: var(--white); font-weight: 700; font-size: 22px; letter-spacing: .2px; }
  .holder__role { color: var(--muted); font-weight: 300; font-size: 12px; margin-top: 4px; }

  .contact { position: absolute; left: 40px; top: 150px; list-style: none; }
  .contact__item {
    display: flex; align-items: flex-start; gap: 12px;
    color: #d8d8d8; font-weight: 300; font-size: 13.5px; line-height: 1.5;
    margin-bottom: 6px;
  }
  .contact__item--address { padding-left: 26px; margin-bottom: 8px; }
  .contact__icon { width: 14px; height: 14px; flex: none; margin-top: 3px; }

  .brand {
    display: flex; align-items: center; gap: 10px;
    font-weight: 700; font-size: 24px; letter-spacing: 1px; text-transform: uppercase;
    line-height: 1.05;
  }
  .brand__mark { width: 18px; height: 18px; flex: none; }
  .card--front .brand { position: absolute; right: 40px; bottom: 110px; color: var(--ink); }
  .card--front .brand__mark { background: var(--ink); }
  .card--back .brand { color: var(--card-gloss); font-size: 30px; }
  .card--back .brand__mark { background: var(--card-gloss); width: 22px; height: 22px; }
</style>
</head>
<body>
  <section class="card card--front">
    <svg class="card__curve" viewBox="0 0 360 630" aria-hidden="true">
      <path d="M0,560 C50,420 190,300 360,288 L360,630 L0,630 Z" fill="#ffffff"/>
      <path d="M20,520 C80,380 200,280 360,262 L360,272 C210,292 95,390 20,520 Z" fill="#ffffff"/>
    </svg>

    <header class="holder">
      <h1 class="holder__name">Ted Galloway</h1>
      <p class="holder__role">Owner</p>
    </header>

    <ul class="contact">
      <li class="contact__item contact__item--address">7-4812 Fernhollow Road,<br>Abbotsford, BC, V3K 8R2</li>
      <li class="contact__item">
        <svg class="contact__icon" viewBox="0 0 16 16"><path d="M4 1l3 3-2 2c1 2 3 4 5 5l2-2 3 3-2 3C7 15 1 9 1 3z" fill="#d8d8d8"/></svg>
        604-712-3390
      </li>
      <li class="contact__item">
        <svg class="contact__icon" viewBox="0 0 16 16"><rect x="4" y="1" width="8" height="14" rx="1.5" fill="none" stroke="#d8d8d8" stroke-width="1.5"/><circle cx="8" cy="12.5" r="1" fill="#d8d8d8"/></svg>
        604-947-2164
      </li>
      <li class="contact__item">
        <svg class="contact__icon" viewBox="0 0 16 16"><rect x="1" y="3" width="14" height="10" rx="1" fill="#d8d8d8"/><path d="M1.5 3.5L8 9l6.5-5.5" fill="none" stroke="#1d1d1f" stroke-width="1.3"/></svg>
        ted@resinworkshub.ca
      </li>
      <li class="contact__item">
        <svg class="contact__icon" viewBox="0 0 16 16"><circle cx="8" cy="8" r="6.5" fill="none" stroke="#d8d8d8" stroke-width="1.4"/><path d="M1.5 8h13M8 1.5c-3 3.5-3 9.5 0 13M8 1.5c3 3.5 3 9.5 0 13" fill="none" stroke="#d8d8d8" stroke-width="1.1"/></svg>
        www.resinworkshub.ca
      </li>
    </ul>

    <div class="brand"><span class="brand__mark"></span><span>Resinworks<br>Hub</span></div>
  </section>

  <section class="card card--back">
    <div class="brand"><span class="brand__mark"></span><span>Resinworks<br>Hub</span></div>
  </section>
</body>
</html>
```